Business card for Bio pharmaceutical company

Hello,
We are a bio pharmaceutical contract manufacturing company in Brisbane, Australia. Can you please create a new business card design. Please go to our website for colours http://www.corvalinbio.com.au.
On the back can you include the cartoon mascot Tobi Tumlo and the tagline
"A Global Biopharmaceutical Contract Development Manufacturing Company"
Target Market(s)
Biotechnology
Industry/Entity Type
Pharmaceutical
Contact Information for Business Card
Maren Holtby
Business Development Manager
maren.holtby@corvalinbio.com.au
1947 Kestrel Road Marlow Queesnland 4183 Australia
T: +61 7 3951 4820
M +61 415 206 718
F +61 7 3842 6093
www.corvalinbio.com.au

```html
<!DOCTYPE html>
<html lang="en">
<head>
<meta charset="utf-8">
<title>Corvalin Bio – Business Card</title>
<link rel="stylesheet" href="https://fonts.googleapis.com/css2?family=Exo+2:wght@600&family=Michroma&display=swap">
<style>
  :root {
    --brand-blue: #0d5274;
    --brand-lime: #b3cb37;
    --card-white: #ffffff;
    --backdrop: #9c9d9e;
    --ink-light: #ffffff;
  }
  html, body {
    margin: 0;
    padding: 0;
    width: 1200px;
    height: 771px;
    overflow: hidden;
    background: var(--backdrop);
  }
  .sheet {
    position: relative;
    width: 1200px;
    height: 771px;
  }
  .card {
    position: absolute;
    top: 231px;
    width: 540px;
    height: 309px;
    background: var(--card-white);
    overflow: hidden;
    box-shadow: 0 6px 18px rgba(0,0,0,0.22);
  }
  .card--details { left: 40px; }
  .card--brand { left: 620px; }

  .card__art {
    position: absolute;
    inset: 0;
    width: 540px;
    height: 309px;
  }
  .band { fill: var(--brand-blue); }
  .swoosh { fill: var(--brand-lime); }

  .wordmark {
    position: absolute;
    display: flex;
    align-items: center;
    gap: 12px;
    font-family: "Exo 2", sans-serif;
    font-weight: 600;
    color: var(--brand-blue);
    white-space: nowrap;
    letter-spacing: -0.5px;
  }
  .wordmark__square {
    display: block;
    background: var(--brand-lime);
  }
  .card--details .wordmark {
    top: 42px;
    left: 232px;
    font-size: 38px;
  }
  .card--details .wordmark__square { width: 22px; height: 22px; }

  .card--brand .wordmark {
    top: 176px;
    left: 42px;
    font-size: 52px;
  }
  .card--brand .wordmark__square { width: 30px; height: 30px; }

  .contact {
    position: absolute;
    top: 138px;
    left: 18px;
    margin: 0;
    padding: 0;
    list-style: none;
    font-family: "Michroma", sans-serif;
    font-size: 7.5px;
    line-height: 13px;
    color: var(--ink-light);
    text-transform: uppercase;
    letter-spacing: 0.4px;
  }
  .contact__item {
    display: flex;
    align-items: center;
    gap: 6px;
  }
  .contact__icon {
    width: 9px;
    height: 9px;
    flex: none;
  }
  .contact__icon circle { fill: var(--ink-light); }
  .contact__icon path { fill: none; stroke: var(--brand-blue); stroke-width: 1.1; }
  .contact__item--plain { padding-left: 15px; }
  .contact__item--web { text-transform: lowercase; }

  .person {
    position: absolute;
    right: 112px;
    bottom: 22px;
    text-align: right;
    font-family: "Michroma", sans-serif;
    color: var(--ink-light);
    text-transform: uppercase;
  }
  .person__name {
    margin: 0;
    font-size: 10px;
    letter-spacing: 1.5px;
  }
  .person__role {
    margin: 3px 0 0;
    font-size: 6.5px;
    letter-spacing: 1.6px;
  }

  .mascot {
    position: absolute;
    top: 30px;
    left: 392px;
    width: 112px;
    height: 132px;
    border-radius: 8px;
    background: linear-gradient(160deg, #d7e49a 0%, #8fb4c6 100%);
  }
  .tagline {
    position: absolute;
    top: 252px;
    left: 44px;
    width: 460px;
    margin: 0;
    font-family: "Michroma", sans-serif;
    font-size: 8px;
    letter-spacing: 0.6px;
    line-height: 12px;
    color: var(--brand-blue);
    text-transform: uppercase;
  }
</style>
</head>
<body>
<main class="sheet">

  <section class="card card--details" aria-label="Business card, contact side">
    <svg class="card__art" viewBox="0 0 540 309" aria-hidden="true">
      <path class="swoosh" d="M92,112 C230,98 360,150 440,309 L432,309 C350,160 230,108 92,112 Z"/>
      <path class="band" d="M0,122 C190,112 360,170 462,309 L0,309 Z"/>
    </svg>

    <div class="wordmark">
      <span class="wordmark__name">Corvalin Bio</span>
      <span class="wordmark__square"></span>
    </div>

    <ul class="contact">
      <li class="contact__item">
        <svg class="contact__icon" viewBox="0 0 10 10"><circle cx="5" cy="5" r="5"/><path d="M5,7.5 C3,5 3,4 5,2.5 C7,4 7,5 5,7.5 Z"/></svg>
        1947 Kestrel Road Marlow
      </li>
      <li class="contact__item contact__item--plain">Queesnland 4183 Australia</li>
      <li class="contact__item">
        <svg class="contact__icon" viewBox="0 0 10 10"><circle cx="5" cy="5" r="5"/><path d="M3,2.5 L4,4.5 L3.5,5 Q4.5,6.5 5.5,6.5 L6,6 L7.5,7 Q6,8 4.5,7 Q2.5,5.5 3,2.5 Z"/></svg>
        T +61 7 3951 4820
      </li>
      <li class="contact__item">
        <svg class="contact__icon" viewBox="0 0 10 10"><circle cx="5" cy="5" r="5"/><path d="M3.5,2.5 H6.5 V7.5 H3.5 Z"/></svg>
        M +61 415 206 718
      </li>
      <li class="contact__item">
        <svg class="contact__icon" viewBox="0 0 10 10"><circle cx="5" cy="5" r="5"/><path d="M2.8,4 H7.2 V7 H2.8 Z M3.8,4 V2.5 H6.2 V4"/></svg>
        F +61 7 3842 6093
      </li>
      <li class="contact__item contact__item--web">
        <svg class="contact__icon" viewBox="0 0 10 10"><circle cx="5" cy="5" r="5"/><path d="M2.5,3.2 H7.5 V6.8 H2.5 Z M2.5,3.2 L5,5.2 L7.5,3.2"/></svg>
        maren.holtby@corvalinbio.com.au
      </li>
      <li class="contact__item contact__item--web">
        <svg class="contact__icon" viewBox="0 0 10 10"><circle cx="5" cy="5" r="5"/><path d="M5,2.3 A2.7,2.7 0 1,0 5.01,2.3 Z M2.3,5 H7.7"/></svg>
        www.corvalinbio.com.au
      </li>
    </ul>

    <div class="person">
      <p class="person__name">Maren Holtby</p>
      <p class="person__role">Business Development Manager</p>
    </div>
  </section>

  <section class="card card--brand" aria-label="Business card, brand side">
    <div class="mascot" role="img" aria-label="Company cartoon mascot"></div>
    <div class="wordmark">
      <span class="wordmark__name">Corvalin Bio</span>
      <span class="wordmark__square"></span>
    </div>
    <p class="tagline">A Global Biopharmaceutical Contract Development Manufacturing Company</p>
  </section>

</main>
</body>
</html>
```